Website design for legal tech start up in Switzerland (B2B)

We are for a legal tech start up in Switzerland called KOVA. We have been running since August 2016. This will be our first live website.

We need a website designed and business card design for our start-up in Switzerland. We also need the Web design to be converted into HTML and CSS files.

Function of website:
• To inform potential customers of our services
• Form a key part of our digital marketing and sales footprint.
• Branding

Please find attached logo.
Updates

Project Deadline Extended Reason: Giving us time to review submissions and provide opportunity for more submissions. Added Thursday, February 16, 2017

Project Deadline Extended
Reason: Looking for more idea's not necessarily set on blue and grey colours only.

Target Market(s)

B2B tech powered legal services.

Industry/Entity Type

Legal

Contact Information for Business Card

Lean and slick design.

Coding

Coded - Design and coding required

Number of Pages Required

5+ page

Requirements
Must have
• VERY LEAN AND CLEAN DESIGN!
• We have received many great standard designs, but we are looking for something more out-of-the box: You can get inspiration from these designs: http://www.pixelvane.com/websites/clean/
• Thanks!!
• Easy content management system
• Well structured coding for additional development
• Responsive webpage for all types of devices
• SEO optimized
• Tabs (Home, services, team, careers, blog, contact us)
• Colour scheme complementary to logo
Nice to have
• Look and Design - Approachable, High-tech, Modern
• Easy to add chat bot capability in future
Should not have
• Too busy/ too much clutter
• Not take to long to load

```html
<!DOCTYPE html>
<html lang="en">
<head>
<meta charset="utf-8">
<title>KOVA – Legal Startup Services</title>
<link href="https://fonts.googleapis.com/css2?family=Open+Sans:wght@400;600;700;800&display=swap" rel="stylesheet">
<style>
:root{
  --navy:#1f3a5a;
  --ink:#2b3440;
  --text:#5b6470;
  --muted:#8a919a;
  --line:#dcdfe3;
  --band:#eef0f2;
  --white:#ffffff;
  --social:#2f8fd8;
  --social-red:#e0533f;
}
*{box-sizing:border-box;margin:0;padding:0}
html,body{width:1200px;height:3488px;overflow:hidden}
body{font-family:"Open Sans",Arial,sans-serif;color:var(--text);background:var(--white);font-size:13px;line-height:1.6}
.wordmark{font-weight:800;color:var(--ink);letter-spacing:2px}
.btn{display:inline-block;background:var(--navy);color:var(--white);font-size:10px;font-weight:700;letter-spacing:1px;padding:7px 16px;text-transform:uppercase}
.section-title{text-align:center;font-size:26px;font-weight:600;color:var(--ink);letter-spacing:1px;text-transform:uppercase}
.dot{display:inline-block;width:22px;height:22px;border-radius:50%;background:var(--social)}
.dot.red{background:var(--social-red)}

/* header */
.site-header{height:120px;position:relative;padding:0 128px}
.site-header .wordmark{position:absolute;left:128px;top:22px;font-size:56px;line-height:1}
.top-contact{position:absolute;right:128px;top:14px;display:flex;gap:18px;align-items:center;font-size:12px;color:var(--muted)}
.top-contact .sq{width:18px;height:18px;background:var(--ink);border-radius:2px;display:inline-block}
.main-nav{position:absolute;right:128px;top:66px;display:flex;gap:6px}
.main-nav a{font-size:13px;color:var(--ink);padding:7px 16px;text-decoration:none}
.main-nav a.active{background:var(--navy);color:var(--white)}

/* hero */
.hero{height:520px;position:relative;background:linear-gradient(180deg,#7fa6cf 0%,#b9cfe3 45%,#a79683 70%,#6e6656 100%)}
.hero-copy{position:absolute;left:150px;top:100px}
.hero-copy h1{font-size:40px;font-weight:800;color:var(--white);letter-spacing:1px}
.hero-copy p{margin-top:10px;background:rgba(60,66,74,.75);color:var(--white);font-size:15px;padding:8px 14px}
.hero-dots{position:absolute;bottom:26px;left:50%;transform:translateX(-50%);display:flex;gap:8px}
.hero-dots span{width:10px;height:10px;border-radius:50%;background:rgba(255,255,255,.6)}
.hero-dots span.on{background:var(--white)}

/* services */
.services{height:700px;padding-top:68px}
.services .intro{text-align:center;margin-top:14px;font-size:14px}
.service-grid{width:720px;margin:40px auto 0;display:grid;grid-template-columns:repeat(3,240px)}
.service{height:230px;display:flex;flex-direction:column;align-items:center;justify-content:center;gap:18px;border-right:1px solid var(--line);border-bottom:1px solid var(--line)}
.service:nth-child(3n){border-right:none}
.service:nth-child(n+4){border-bottom:none}
.service span{font-size:14px;color:var(--navy)}
.service svg{width:64px;height:64px;fill:none;stroke:var(--ink);stroke-width:2}

/* welcome */
.welcome{height:400px;background:var(--band);position:relative}
.welcome-text{position:absolute;left:128px;top:40px;width:400px}
.welcome-text h2{font-size:34px;font-weight:700;color:var(--ink);line-height:1.1}
.welcome-text .wordmark{font-size:80px;line-height:1}
.welcome-text p{margin-top:24px;font-size:13px}
.welcome-text .btn{margin-top:18px}
.welcome-divider{position:absolute;left:620px;top:40px;width:1px;height:320px;background:var(--line)}
.features{position:absolute;left:690px;top:50px;width:420px;list-style:none}
.features li{display:flex;gap:16px;margin-bottom:20px}
.features svg{width:26px;height:26px;flex:none;fill:none;stroke:var(--navy);stroke-width:2}
.features b{display:block;font-size:11px;color:var(--ink);letter-spacing:.5px}
.features small{font-size:12px}

/* team */
.team{height:660px;padding-top:60px}
.team-grid{width:960px;margin:56px auto 0;display:grid;grid-template-columns:repeat(4,240px)}
.member{text-align:center}
.member .photo{width:190px;height:190px;border-radius:50%;margin:0 auto;border:6px solid var(--white);box-shadow:0 0 0 1px var(--line);background:radial-gradient(circle at 50% 40%,#c9d7e6,#6f8aa6)}
.member .socials{margin-top:-12px;display:flex;justify-content:center;gap:6px;position:relative}
.member h3{margin-top:12px;font-size:12px;font-weight:700;color:var(--ink)}
.member .role{font-size:12px;color:var(--muted)}
.member p{margin:8px auto 0;width:170px;font-size:12px}
.member .btn{margin-top:14px}

/* blog */
.blog{height:600px;background:var(--band);padding-top:50px}
.blog-grid{width:936px;margin:36px auto 0;display:grid;grid-template-columns:repeat(3,296px);gap:24px}
.post{background:var(--white)}
.post .thumb{height:220px;background:linear-gradient(135deg,#8da2b8,#d8dee6 60%,#a3aebb)}
.post .body{padding:16px 20px 22px}
.post h3{font-size:15px;font-weight:600;color:var(--navy);line-height:1.35}
.post p{margin-top:8px;font-size:12px}
.post .btn{margin-top:14px}

/* footer */
.site-footer{height:360px;position:relative}
.footer-brand{position:absolute;left:128px;top:70px;text-align:center;width:220px}
.footer-brand .wordmark{font-size:60px;line-height:1}
.footer-brand h4{margin-top:60px;font-size:11px;color:var(--navy);letter-spacing:1px}
.footer-brand .row{margin-top:10px;display:flex;justify-content:center;gap:8px}
.footer-col{position:absolute;top:56px}
.footer-col h4{font-size:12px;color:var(--ink);letter-spacing:1px;margin-bottom:14px}
.footer-menu{left:572px}
.footer-menu a{display:block;font-size:12px;color:var(--text);text-decoration:none;line-height:2}
.footer-contact{left:820px}
.footer-contact div{display:flex;gap:12px;align-items:flex-start;font-size:12px;margin-bottom:16px}
.footer-contact svg{width:22px;height:22px;flex:none}
.copyright{height:48px;border-top:1px solid var(--line);text-align:center;font-size:11px;line-height:48px;color:var(--muted)}
</style>
</head>
<body>

<header class="site-header">
  <div class="wordmark">KOVA</div>
  <div class="top-contact">
    <span>info@kova.ch</span>
    <span>(044) 555 0198</span>
    <span class="sq"></span><span class="sq"></span><span class="sq"></span>
  </div>
  <nav class="main-nav">
    <a class="active" href="#">Home</a><a href="#">Services</a><a href="#">Team</a><a href="#">Careers</a><a href="#">Blog</a><a href="#">Contact us</a>
  </nav>
</header>

<section class="hero" role="img" aria-label="Photograph of a Swiss old town with a church spire under a blue sky">
  <div class="hero-copy">
    <h1>LEGAL STARTUP</h1>
    <p>Lorem ipsum is simply dummy text of the printing</p>
  </div>
  <div class="hero-dots"><span></span><span class="on"></span><span></span><span></span></div>
</section>

<section class="services">
  <h2 class="section-title">Legal Startup Services</h2>
  <p class="intro">Contrary to popular belief, Lorem Ipsum is not simply random text.<br>It has roots in a piece of classical Latin literature</p>
  <div class="service-grid">
    <div class="service"><svg viewBox="0 0 64 64"><rect x="8" y="20" width="48" height="34" rx="3"/><path d="M24 20v-8h16v8M8 34h48"/></svg><span>Business Disputes</span></div>
    <div class="service"><svg viewBox="0 0 64 64"><rect x="14" y="6" width="36" height="52" rx="3"/><rect x="20" y="12" width="24" height="10"/><path d="M22 30h4M30 30h4M38 30h4M22 38h4M30 38h4M38 38h4M22 46h4M30 46h4M38 46h4"/></svg><span>Accounting Services</span></div>
    <div class="service"><svg viewBox="0 0 64 64"><path d="M14 6h28l8 8v44H14z"/><path d="M22 22h20M22 30h20M22 38h12"/><path d="M36 52l16-16 4 4-16 16h-4z"/></svg><span>Agreements/Contracts</span></div>
    <div class="service"><svg viewBox="0 0 64 64"><path d="M32 6a16 16 0 0 0-9 29v9h18v-9A16 16 0 0 0 32 6z"/><path d="M24 50h16M26 56h12"/></svg><span>Intellectual Property</span></div>
    <div class="service"><svg viewBox="0 0 64 64"><circle cx="32" cy="18" r="10"/><path d="M32 13v10M6 44l12-6h14l6 4H24M38 42l14-8 6 4-20 16H10"/></svg><span>Startup Financing</span></div>
    <div class="service"><svg viewBox="0 0 64 64"><path d="M32 58V22M32 36c-10 0-16-6-16-14 8 0 16 4 16 14zM32 30c8 0 14-6 14-14-8 0-14 4-14 14zM18 58h28"/></svg><span>Raising Capital</span></div>
  </div>
</section>

<section class="welcome">
  <div class="welcome-text">
    <h2>Welcome to</h2>
    <div class="wordmark">KOVA</div>
    <p>It is a long established fact that a reader will be distracted by the readable content of a page when looking at its layout. The point of using Lorem Ipsum is that it has a more-or-less normal distribution of letters, as opposed to using content here, making it look like readable.</p>
    <span class="btn">Read more →</span>
  </div>
  <div class="welcome-divider"></div>
  <ul class="features">
    <li><svg viewBox="0 0 26 26"><circle cx="13" cy="13" r="10"/><path d="M8 13l4 4 6-8"/></svg><div><b>COST- EFFICIENT</b><small>There are many variations of passages of Lorem Ipsum</small></div></li>
    <li><svg viewBox="0 0 26 26"><circle cx="13" cy="13" r="10"/><path d="M13 7v6l4 3"/></svg><div><b>TIME SAVING</b><small>There are many variations of passages of Lorem Ipsum</small></div></li>
    <li><svg viewBox="0 0 26 26"><circle cx="13" cy="13" r="10"/><circle cx="13" cy="13" r="4"/></svg><div><b>OUR MISSION</b><small>It is a long established fact that a reader will be distracted</small></div></li>
    <li><svg viewBox="0 0 26 26"><circle cx="9" cy="9" r="4"/><circle cx="18" cy="9" r="4"/><path d="M2 22c0-5 4-8 7-8s7 3 7 8M12 16c2-2 4-2 6-2 3 0 6 3 6 8"/></svg><div><b>TEAM</b><small>Combined with a handful of model sentences</small></div></li>
    <li><svg viewBox="0 0 26 26"><path d="M4 6h18v12H10l-6 4z"/></svg><div><b>GET SUPPORT</b><small>Lorem ipsum will uncover many web sites still in</small></div></li>
  </ul>
</section>

<section class="team">
  <h2 class="section-title">Our Team</h2>
  <div class="team-grid">
    <div class="member"><div class="photo" role="img" aria-label="Portrait photo of a team member in a suit"></div><div class="socials"><span class="dot"></span><span class="dot"></span></div><h3>MARTIN KELLER</h3><div class="role">CEO</div><p>There are many variations of passages of Lorem</p><span class="btn">View Bio</span></div>
    <div class="member"><div class="photo" role="img" aria-label="Portrait photo of a team member in a suit"></div><div class="socials"><span class="dot"></span><span class="dot"></span></div><h3>LUKAS BRUNNER</h3><div class="role">Attorney</div><p>There are many variations of passages of Lorem</p><span class="btn">View Bio</span></div>
    <div class="member"><div class="photo" role="img" aria-label="Portrait photo of a team member in a suit"></div><div class="socials"><span class="dot"></span><span class="dot"></span></div><h3>DANIEL MEIER</h3><div class="role">Attorney</div><p>There are many variations of passages of Lorem</p><span class="btn">View Bio</span></div>
    <div class="member"><div class="photo" role="img" aria-label="Portrait photo of a team member in business attire"></div><div class="socials"><span class="dot"></span><span class="dot"></span></div><h3>NINA</h3><div class="role">Attorney</div><p>There are many variations of passages of Lorem</p><span class="btn">View Bio</span></div>
  </div>
</section>

<section class="blog">
  <h2 class="section-title">Latest Blog</h2>
  <div class="blog-grid">
    <article class="post"><div class="thumb" role="img" aria-label="Photo of business people in a meeting"></div><div class="body"><h3>It is a long established fact that a reader will be distracted</h3><p>There are many variations of passages of Lorem Ipsum available</p><span class="btn">Read more</span></div></article>
    <article class="post"><div class="thumb" role="img" aria-label="Photo of a team standing together in an office"></div><div class="body"><h3>There are many variations of passages of Lorem Ipsum</h3><p>There are many variations of passages of Lorem Ipsum available</p><span class="btn">Read more</span></div></article>
    <article class="post"><div class="thumb" role="img" aria-label="Photo of colleagues working around a desk"></div><div class="body"><h3>Sed ut perspiciatis unde omnis iste natus error</h3><p>There are many variations of passages of Lorem Ipsum available</p><span class="btn">Read more</span></div></article>
  </div>
</section>

<footer class="site-footer">
  <div class="footer-brand">
    <div class="wordmark">KOVA</div>
    <h4>FOLLOW US</h4>
    <div class="row"><span class="dot"></span><span class="dot"></span><span class="dot red"></span></div>
  </div>
  <div class="footer-col footer-menu">
    <h4>MENU</h4>
    <a href="#">Home</a><a href="#">Services</a><a href="#">Team</a><a href="#">Careers</a><a href="#">Blog</a><a href="#">Contact Us</a>
  </div>
  <div class="footer-col footer-contact">
    <h4>CONTACT US</h4>
    <div><svg viewBox="0 0 22 22"><circle cx="11" cy="11" r="11" fill="#1f3a5a"/><path d="M11 5a4 4 0 0 0-4 4c0 3 4 8 4 8s4-5 4-8a4 4 0 0 0-4-4z" fill="#fff"/></svg><span>12 Seefeldstrasse<br>8008 Zürich, Switzerland</span></div>
    <div><svg viewBox="0 0 22 22"><circle cx="11" cy="11" r="11" fill="#1f3a5a"/><path d="M7 6l3 0 1 3-2 1c1 2 2 3 3 3l1-2 3 1v3c-5 0-9-4-9-9z" fill="#fff"/></svg><span>(044) 555 0198</span></div>
    <div><svg viewBox="0 0 22 22"><circle cx="11" cy="11" r="11" fill="#1f3a5a"/><rect x="6" y="7" width="10" height="8" fill="#fff"/><path d="M6 7l5 4 5-4" stroke="#1f3a5a" fill="none"/></svg><span>info@kova.ch</span></div>
  </div>
</footer>
<div class="copyright">Copyright © 2017 KOVA. All Rights Reserved.</div>

</body>
</html>
```